LinkedIn Banner Design for B2B Consulting Firm

Take the already developed logo (attached) and incorporate it into a creative banner design for placement on LinkedIn (the social media platform targeting business users). The banner will be used on the firm's company profile page on LinkedIn (not yet created).

```html
<!DOCTYPE html>
<html lang="en">
<head>
<meta charset="UTF-8">
<title>Fractional Marketing Services – Profile Banner</title>
<link href="https://fonts.googleapis.com/css2?family=Source+Serif+4:opsz,wght@8..60,400;8..60,700&display=swap" rel="stylesheet">
<style>
  :root {
    --page-bg: #e6e6e6;
    --banner-green: #50634e;
    --ink-white: #ffffff;
    --mist: #c9cfc6;
    --photo-warm: #8a6a4c;
    --photo-cool: #b7c0c8;
  }
  * { margin: 0; padding: 0; box-sizing: border-box; }
  html, body {
    width: 1200px; height: 800px; overflow: hidden;
    background: var(--page-bg);
  }
  .canvas {
    position: relative; width: 1200px; height: 800px;
    display: flex; align-items: center; justify-content: center;
  }
  .banner {
    position: relative; width: 1120px; height: 190px;
    background: var(--banner-green); overflow: hidden;
  }
  .banner-shapes { position: absolute; inset: 0; }
  .headline {
    position: absolute; left: 266px; top: 30px;
    color: var(--ink-white);
    font-family: "Source Serif 4", Georgia, serif;
  }
  .headline-title {
    font-size: 39px; font-weight: 700; line-height: 44px; letter-spacing: 0.2px;
  }
  .headline-sub {
    font-size: 29px; font-weight: 400; line-height: 31px;
  }
</style>
</head>
<body>
<main class="canvas">
  <section class="banner">
    <svg class="banner-shapes" width="1120" height="190" viewBox="0 0 1120 190">
      <defs>
        <linearGradient id="mistFade" x1="0" y1="0" x2="1" y2="0">
          <stop offset="0" stop-color="#50634e"/>
          <stop offset="1" stop-color="#d3d8d0"/>
        </linearGradient>
        <linearGradient id="workspaceTones" x1="0" y1="0" x2="1" y2="1">
          <stop offset="0" stop-color="var(--photo-cool)"/>
          <stop offset="0.5" stop-color="var(--photo-warm)"/>
          <stop offset="1" stop-color="#5b4a3c"/>
        </linearGradient>
      </defs>
      <!-- soft fade notch -->
      <path class="fade-notch" d="M810 0 L895 95 Q907 108 920 95 L1018 0 Z" fill="url(#mistFade)"/>
      <path class="corner-fade" d="M1066 0 L1120 0 L1120 48 L1068 6 Q1062 2 1066 0 Z" fill="#c7cdc4"/>
      <!-- workspace photo window -->
      <g class="photo-window">
        <path d="M1037 -12 Q1047 -12 1055 -4 L1160 100 Q1168 108 1160 116 L1045 231 Q1037 239 1029 231 L914 116 Q906 108 914 100 L1019 -4 Q1027 -12 1037 -12 Z"
              transform="translate(0,30)" fill="var(--ink-white)"/>
        <path role="img" aria-label="Photo of colleagues working at a laptop with coffee and charts on a wooden desk"
              d="M1037 -5 Q1044 -5 1050 1 L1153 104 Q1157 108 1153 112 L1041 224 Q1037 228 1033 224 L921 112 Q917 108 921 104 L1024 1 Q1030 -5 1037 -5 Z"
              transform="translate(0,30)" fill="url(#workspaceTones)"/>
      </g>
      <!-- headline bracket line -->
      <g class="bracket" fill="none" stroke="var(--ink-white)" stroke-width="1.2">
        <path d="M247 51 V134 Q247 147 260 147 H788"/>
      </g>
      <circle cx="247" cy="51" r="4" fill="var(--ink-white)"/>
      <g class="arrow-icon" fill="none" stroke="var(--ink-white)" stroke-width="1.6" stroke-linejoin="round">
        <path d="M791 140 L798 147 L791 154"/>
        <path d="M796 140 L803 147 L796 154"/>
        <path d="M801 140 L808 147 L801 154"/>
      </g>
    </svg>
    <div class="headline">
      <h1 class="headline-title">Fractional Marketing Services</h1>
      <p class="headline-sub">For Private Equity Firms, Family Offices<br>&amp; Investment Banks</p>
    </div>
  </section>
</main>
</body>
</html>
```